Stationery Set for Velmora Company

I need to create full stationery design for my company; Business Cards, Envelops, Letter Heads, Calendar.
In the letter head and Envelops... only contact information and website links.
Our company is a Service Management company with different domains of innovative services including Technology Service Management, Education Services, Outsourcing Management, Events Management.
I need a modern and innovative design specially for the business card. I some transparent designs and I like it, but don't limit your innovation to what I mentioned. Sky is limit for your innovation.

Target Market(s)

Middle East & Africa

Industry/Entity Type

Business Management

Colors
34a7d8
0355a3
85acd3
86cae7
cee9f5
cfdeed
e4daeb
f3f1f8
ecf7fb

Requirements
Must have
• Name, Title, Email, Mobile
Nice to have
• We have multiple locations in USA, KSA, EGY, so I need ideas about how to include all contact details maybe QR / Barcode or something else.
• Please see our locations and contact information: www.brightvelmora.example
Should not have
• Too much text

```html
<!DOCTYPE html>
<html lang="en">
<head>
<meta charset="utf-8">
<title>Velmora Company Stationery</title>
<link href="https://fonts.googleapis.com/css2?family=Arimo:wght@400;700&display=swap" rel="stylesheet">
<style>
:root{
  --bg:#ececec;
  --paper:#ffffff;
  --edge:#dcdcdc;
  --blue-deep:#2f3f9e;
  --blue-sky:#34a7d8;
  --blue-brand:#0355a3;
  --swoosh:#4a4a4a;
  --ink:#333333;
  --ink-soft:#555555;
}
*{margin:0;padding:0;box-sizing:border-box}
html,body{width:1200px;height:937px;overflow:hidden;background:var(--bg);font-family:"Arimo",Arial,sans-serif;color:var(--ink)}
.canvas{position:relative;width:1200px;height:937px}
.sheet{position:absolute;background:var(--paper);border:1px solid var(--edge);overflow:hidden}
.wave{position:absolute;left:0;bottom:0;width:100%}
.brand{font-weight:700;color:var(--blue-brand);white-space:nowrap;display:flex;align-items:center;gap:5px}
.brand .dot{display:inline-block;background:var(--blue-sky);border-radius:50%}
.site{position:absolute;left:0;width:100%;text-align:center;color:#fff;letter-spacing:.28em;font-size:11px}

/* letterhead */
.letterhead{left:185px;top:66px;width:387px;height:546px}
.letterhead .brand{position:absolute;left:18px;top:28px;font-size:15px}
.letterhead .brand .dot{width:9px;height:9px}
.letter{position:absolute;left:36px;top:140px;width:300px;font-size:5.6px;line-height:1.45;color:var(--ink-soft)}
.letter p{margin-bottom:10px}
.letter .gap{margin-bottom:22px}
.letter strong{color:var(--ink)}
.signature{width:42px;height:18px;background:linear-gradient(90deg,#cfcfcf,#e9e9e9);margin:4px 0 8px}
.lh-address{position:absolute;left:16px;bottom:12px;color:#fff;font-size:7.5px;line-height:1.35}
.lh-contacts{position:absolute;right:16px;bottom:10px;color:#fff;font-size:4.6px;line-height:1.9;text-align:right}
.lh-contacts span::after{content:"";display:inline-block;width:4px;height:4px;border-radius:50%;background:#fff;margin-left:4px;vertical-align:middle}

/* folder */
.folder{left:636px;top:40px;width:458px;height:576px}
.folder .brand{position:absolute;left:0;width:100%;top:280px;justify-content:center;font-size:28px}
.folder .brand .dot{width:14px;height:14px}
.folder .site{bottom:14px;font-size:11.5px}

/* cards */
.card{left:46px;width:176px;height:100px;border-radius:8px}
.card-front{top:658px}
.card-front .brand{position:absolute;left:10px;top:10px;font-size:9px}
.card-front .brand .dot{width:6px;height:6px}
.card-person{position:absolute;left:8px;bottom:10px;color:#fff;font-size:4.3px;line-height:1.5}
.card-contacts{position:absolute;right:8px;bottom:10px;color:#fff;font-size:4.3px;line-height:1.6;text-align:right}
.card-back{top:785px}
.card-back .brand{position:absolute;left:0;width:100%;top:42px;justify-content:center;font-size:10px}
.card-back .brand .dot{width:6px;height:6px}

/* envelopes */
.envelope{top:672px;width:431px;height:208px}
.envelope-front{left:266px}
.envelope-front .brand{position:absolute;left:14px;top:22px;font-size:14px}
.envelope-front .brand .dot{width:8px;height:8px}
.envelope-front .site{bottom:12px;font-size:9px}
.envelope-back{left:737px}
.flap{position:absolute;left:0;top:0;width:100%;height:72px;border-radius:0 0 46px 46px;background:linear-gradient(90deg,var(--blue-deep),var(--blue-sky) 55%,var(--blue-deep))}
.envelope-back .site{top:28px;font-size:11px}
</style>
</head>
<body>
<div class="canvas">
  <svg width="0" height="0" style="position:absolute">
    <defs>
      <linearGradient id="band" x1="0" x2="1" y1="0" y2="0">
        <stop offset="0" stop-color="#2f3f9e"/>
        <stop offset=".55" stop-color="#34a7d8"/>
        <stop offset="1" stop-color="#2f3f9e"/>
      </linearGradient>
    </defs>
  </svg>

  <section class="sheet letterhead">
    <div class="brand"><span class="dot"></span>Velmora Company</div>
    <div class="letter">
      <p>July 2, 2012</p>
      <p><strong>Dear Client,</strong><br>ABC Building, def St., Country Name</p>
      <p class="gap">Lorem ipsum is simply dummy text of the printing and typesetting industry. Lorem Ipsum has been the industry's standard dummy text ever since the 1500s, when an unknown printer took a galley of type and scrambled it to make a type specimen book. It has survived not only five centuries, but also the leap into electronic typesetting, remaining essentially unchanged. It was popularised in the 1960s with the release of Letraset sheets containing Lorem Ipsum passages, and more recently with desktop publishing software including versions of Lorem Ipsum.</p>
      <p class="gap">Lorem ipsum is simply dummy text of the printing and typesetting industry. Lorem Ipsum has been the industry's standard dummy text ever since the 1500s, when an unknown printer took a galley of type and scrambled it to make</p>
      <p>Lorem ipsum is simply dummy text of the printing and typesetting industry. Lorem Ipsum has been the industry's standard dummy text ever since the 1500s, when an unknown printer took a galley of type and scrambled it to make a type specimen book. It has survived not only five centuries, but also the leap into electronic typesetting, remaining essentially unchanged. It was popularised in the 1960s with the release of Letraset sheets containing Lorem Ipsum passages, and more recently with desktop publishing software including versions of Lorem Ipsum.</p>
      <p>Best Regards,</p>
      <div class="signature" role="img" aria-label="Handwritten signature"></div>
      <p><strong>Daniel Reyes</strong><br>Director<br><br>ABC Building, def St., Country Name</p>
    </div>
    <svg class="wave" viewBox="0 0 400 90" height="90" preserveAspectRatio="none" aria-hidden="true">
      <path d="M0,34 C130,30 260,2 400,4 L400,16 C260,12 130,42 0,40 Z" fill="var(--swoosh)"/>
      <path d="M0,42 C130,44 260,14 400,18 L400,90 L0,90 Z" fill="url(#band)"/>
    </svg>
    <div class="lh-address">27 Harbor Lane<br>Riverside Road</div>
    <div class="lh-contacts">
      <span>012 345 6789</span><br>
      <span>012 345 6790</span><br>
      <span>012 345 6791</span><br>
      <span>info@brightvelmora.example</span><br>
      <span>www.brightvelmora.example</span>
    </div>
  </section>

  <section class="sheet folder">
    <div class="brand"><span class="dot"></span>Velmora Company</div>
    <svg class="wave" viewBox="0 0 400 92" height="92" preserveAspectRatio="none" aria-hidden="true">
      <path d="M0,30 C130,28 260,0 400,2 L400,14 C260,10 130,38 0,38 Z" fill="var(--swoosh)"/>
      <path d="M0,40 C130,42 260,12 400,16 L400,92 L0,92 Z" fill="url(#band)"/>
    </svg>
    <div class="site">www.brightvelmora.example</div>
  </section>

  <section class="sheet card card-front">
    <div class="brand"><span class="dot"></span>Velmora Company</div>
    <svg class="wave" viewBox="0 0 176 72" height="72" preserveAspectRatio="none" aria-hidden="true">
      <path d="M0,18 C60,6 120,0 176,4 L176,12 C120,8 60,14 0,26 Z" fill="var(--swoosh)"/>
      <path d="M0,28 C60,16 120,10 176,14 L176,72 L0,72 Z" fill="url(#band)"/>
    </svg>
    <div class="card-person">DANIEL REYES<br>Managing Director<br><br>27 Harbor Lane<br>Riverside Road</div>
    <div class="card-contacts">012 345 6789<br>012 345 6790<br>012 345 6791<br>info@brightvelmora.example<br>www.brightvelmora.example</div>
  </section>

  <section class="sheet card card-back">
    <div class="brand"><span class="dot"></span>Velmora Company</div>
  </section>

  <section class="sheet envelope envelope-front">
    <div class="brand"><span class="dot"></span>Velmora Company</div>
    <svg class="wave" viewBox="0 0 431 96" height="96" preserveAspectRatio="none" aria-hidden="true">
      <path d="M0,30 C140,26 280,0 431,2 L431,14 C280,10 140,38 0,38 Z" fill="var(--swoosh)"/>
      <path d="M0,40 C140,42 280,12 431,16 L431,96 L0,96 Z" fill="url(#band)"/>
    </svg>
    <div class="site">www.brightvelmora.example</div>
  </section>

  <section class="sheet envelope envelope-back">
    <div class="flap"></div>
    <div class="site">www.brightvelmora.example</div>
  </section>
</div>
</body>
</html>
```